Summit Builders Web Site / Business Cards

Construction Company that specializes in Water and Fire Damage, Residential ReModels, Landscaping and Building ADU (Accessory Dwelling Unit)

Growing and changing families often need additional space, and a remodeling project can often provide that. Adding a new area, or repurposing an existing one can satisfy this requirement.

Other times, homeowners want to update the look in their kitchen or bathroom with more than just a change of cabinetry or vanity doors and drawers. Whatever your needs are, Summit Builders has skilled workers who are bonded and insured, and ready to make your dreams and visions a reality.

Target Market(s)

Home Owners

Industry/Entity Type

Construction Company

Contact Information for Business Card

Center Logo with our information on the corners

Back side to be Logo Only
Contact Info
CSLB License # 2418596
info@summitbuildersca.example
www.summitbuildersca.example

Coding

Coded - Design and coding required

Number of Pages Required

5+ page

Font styles to use
Serif
Sans Serif

Requirements
Must have
• Using our Logo Colors
Home
About Us
Services
Projects / Portfolio
Contact Us
Nice to have
• Colors matching our Logo
Should not have
• Black because it doesnt match our logo

```html
<!DOCTYPE html>
<html lang="en">
<head>
<meta charset="utf-8">
<title>Summit Builders</title>
<link href="https://fonts.googleapis.com/css2?family=Poppins:wght@400;500;600&family=Lato:ital,wght@0,400;0,700;1,400&family=Roboto+Condensed:wght@700&display=swap" rel="stylesheet">
<style>
:root{
  --orange:#f15a24;
  --orange-dark:#c94112;
  --navy:#0b1030;
  --navy-2:#12183d;
  --text:#3a3a3a;
  --muted:#6b6b6b;
  --grey-bg:#eeecea;
  --line:#d9d9d9;
  --white:#ffffff;
}
*{margin:0;padding:0;box-sizing:border-box}
html,body{width:1200px;height:4491px;overflow:hidden}
body{position:relative;font-family:'Lato',sans-serif;color:var(--text);background:var(--white)}
.abs{position:absolute}
a{color:inherit;text-decoration:none}

/* top bar */
.topbar{left:0;top:0;width:1200px;height:44px;background:var(--navy)}
.topbar .links{left:115px;top:14px;font-size:11px;color:#8b8fa6;display:flex;gap:24px}
.topbar .social{right:120px;top:14px;display:flex;gap:24px}
.topbar .social span{width:10px;height:10px;border-radius:50%;background:#6b708a;display:block}

/* header */
.logo{display:flex;align-items:center;gap:8px}
.logo .mark{width:14px;height:14px;background:var(--orange)}
.logo .name{font-family:'Poppins',sans-serif;font-weight:600;letter-spacing:1px;color:var(--navy);font-size:18px;text-transform:uppercase}
.header-logo{left:108px;top:78px}
.contact-item{top:78px;font-size:11px}
.contact-item .lab{color:var(--orange);display:flex;align-items:center;gap:6px}
.contact-item .val{color:#111;font-weight:700;margin-top:11px;font-size:11.5px}

/* nav */
.nav{left:108px;top:148px;width:984px;height:79px;background:var(--navy);z-index:3}
.nav ul{list-style:none;display:flex;position:absolute;left:62px;top:28px;gap:0}
.nav li{font-size:15px;color:#fff;margin-right:50px;position:relative}
.nav li.active{color:var(--orange)}
.nav li.active::after{content:"";position:absolute;left:-4px;right:-4px;top:30px;height:2px;background:var(--orange)}
.nav .cta{right:0;top:10px;width:160px;height:60px;border:1px solid var(--orange);color:var(--orange);font-family:'Poppins',sans-serif;font-size:16px;display:flex;align-items:center;justify-content:center;right:20px}

/* hero */
.hero{left:0;top:187px;width:1200px;height:558px;background:linear-gradient(180deg,#3e4046 0%,#5a554f 45%,#2f2c2c 100%)}
.hero::after{content:"";position:absolute;inset:0;background:rgba(11,16,48,.35)}
.hero-title{left:0;top:358px;width:1200px;text-align:center;font-family:'Poppins',sans-serif;font-size:52px;color:#fff;font-weight:400;z-index:2}
.hero-text{left:230px;top:436px;width:740px;text-align:center;color:#fff;font-size:16px;line-height:26px;z-index:2}
.btn{background:var(--orange);color:#fff;font-family:'Poppins',sans-serif;font-weight:600;font-size:15px;display:flex;align-items:center;justify-content:center}
.hero-btn{left:525px;top:507px;width:148px;height:55px;z-index:2}
.mouse{left:590px;top:677px;z-index:2}
.side-social{right:0;top:305px;width:36px;z-index:4}
.side-social span{display:block;height:34px;margin-bottom:1px}

/* section titles */
.sec-mark{width:26px;height:20px;border-bottom:3px solid var(--orange);border-left:3px solid var(--orange);border-right:3px solid var(--orange)}
.sec-title{left:0;width:1200px;text-align:center;font-family:'Poppins',sans-serif;font-size:35px;color:#1b1b1b;font-weight:400}
.sec-title em{font-style:normal;color:var(--orange)}

/* specializes */
.spec-box{top:959px;width:230px;height:178px;border:1px solid #cfcfcf;text-align:center}
.spec-box svg{margin-top:22px}
.spec-box p{color:var(--orange);font-family:'Poppins',sans-serif;font-size:17px;line-height:26px;margin-top:10px}

/* who we are */
.who{left:0;top:1230px;width:1200px;height:585px;background:var(--grey-bg)}
.ph{position:absolute}
.who h2{font-family:'Poppins',sans-serif;font-weight:500;font-size:35px;color:#1b1b1b}
.who h2 em{font-style:normal;color:var(--orange)}
.who .sub{font-size:23px;color:#555;margin-top:6px;font-family:'Lato',sans-serif}
.who .para{font-size:13.5px;line-height:26px;color:#555;margin-top:16px;width:450px}
.who .feat{display:grid;grid-template-columns:247px 200px;row-gap:22px;margin-top:26px;color:var(--orange);font-size:13.5px}

/* what we do */
.work-img{width:310px;height:181px}
.work-label{width:310px;text-align:center;color:var(--orange);font-family:'Roboto Condensed',sans-serif;font-weight:700;font-size:16px;text-transform:uppercase}

/* stats */
.stats{left:0;top:2574px;width:1200px;height:286px;background:linear-gradient(100deg,#e8561b 0%,#f26a25 45%,#e35b1c 70%,#d9541a 100%)}
.stat{width:260px;text-align:center;color:#fff}
.stat .num{font-family:'Poppins',sans-serif;font-size:36px;font-weight:400}
.stat .lab{font-family:'Roboto Condensed',sans-serif;font-weight:700;font-size:20px;margin-top:4px}

/* testimonials */
.avatar{width:178px;height:178px;border-radius:50%}
.quote{font-style:italic;font-size:12px;line-height:24px;color:#666;width:270px}
.t-name{font-family:'Roboto Condensed',sans-serif;font-size:16px;color:#444;font-weight:700}
.stars{color:var(--orange);font-size:17px;letter-spacing:3px}
.dots span{display:inline-block;width:9px;height:9px;border-radius:50%;background:#c9c9c9;margin:0 3px}
.dots span.on{background:var(--orange)}

/* projects */
.proj{position:absolute}

/* footer */
.footer{left:0;top:4105px;width:1200px;height:386px;background:var(--navy)}
.footer .logo .name{color:#fff}
.footer h4{font-family:'Roboto Condensed',sans-serif;font-weight:700;font-size:16px;color:#fff;letter-spacing:.3px}
.footer .f-text{color:#fff;font-size:15px;line-height:26px}
.footer ul{list-style:none}
.footer .ql li{color:#fff;font-size:15px;line-height:26px}
.footer .ci li{color:#fff;font-size:15px;line-height:25px;display:flex;gap:14px;margin-bottom:18px}
.footer .license{color:var(--orange);font-size:15px}
.footer .rule{left:100px;top:4386px;width:1000px;height:1px;background:#2a3058}
.footer .copy{left:0;top:4408px;width:1200px;text-align:center;color:#fff;font-family:'Poppins',sans-serif;font-size:16px}
</style>
</head>
<body>

<!-- top bar -->
<div class="abs topbar">
  <div class="abs links"><span>Career</span><span>Terms of service</span><span>Refund policy</span></div>
  <div class="abs social"><span></span><span></span><span></span><span></span></div>
</div>

<!-- header -->
<div class="abs header-logo logo"><span class="mark"></span><span class="name">Summit Builders</span></div>
<div class="abs contact-item" style="left:328px">
  <div class="lab"><svg width="10" height="10" viewBox="0 0 24 24"><path fill="#f15a24" d="M6.6 10.8a15 15 0 006.6 6.6l2.2-2.2a1 1 0 011-.25 11 11 0 003.6.6 1 1 0 011 1V20a1 1 0 01-1 1A17 17 0 013 4a1 1 0 011-1h3.5a1 1 0 011 1 11 11 0 00.6 3.6 1 1 0 01-.25 1z"/></svg>Call Us anytime</div>
  <div class="val" style="margin-left:16px">+1 555 014 2207</div>
</div>
<div class="abs contact-item" style="left:550px">
  <div class="lab"><svg width="11" height="9" viewBox="0 0 24 18"><path fill="#f15a24" d="M0 0h24v18H0z"/><path fill="none" stroke="#fff" stroke-width="2" d="M1 1l11 9 11-9"/></svg>Email Address</div>
  <div class="val" style="margin-left:20px">info@summitbuildersca.example</div>
</div>
<div class="abs contact-item" style="left:836px">
  <div class="lab"><svg width="9" height="12" viewBox="0 0 24 32"><path fill="#f15a24" d="M12 0a12 12 0 0112 12c0 9-12 20-12 20S0 21 0 12A12 12 0 0112 0zm0 7a5 5 0 100 10 5 5 0 000-10z"/></svg>Address</div>
  <div class="val" style="margin-left:16px">1520 Ridgeview Ave Fairmont, CA 92705</div>
</div>

<!-- nav -->
<nav class="abs nav">
  <ul>
    <li class="active">Home</li><li>About us</li><li>Services</li><li>Projects/ Portfolio</li><li>Contact us</li>
  </ul>
  <a class="abs cta">Get In Touch</a>
</nav>

<!-- hero -->
<div class="abs hero" role="img" aria-label="Construction site with workers in hard hats, darkened"></div>
<h1 class="abs hero-title">SUMMIT BUILDERS</h1>
<p class="abs hero-text">Lorem ipsum dolor sit amet, consectetur adipiscing elit, sed do eiusmod tempor incididunt ut labore et dolore magna aliqua.</p>
<a class="abs btn hero-btn">GET STARTED</a>
<svg class="abs mouse" width="20" height="32" viewBox="0 0 20 32"><rect x="1" y="1" width="18" height="30" rx="9" fill="none" stroke="#fff" stroke-width="2"/><line x1="10" y1="7" x2="10" y2="13" stroke="#fff" stroke-width="2"/></svg>
<div class="abs side-social">
  <span style="background:#2d4a8f"></span><span style="background:#2a9bd6"></span><span style="background:#c9295a"></span><span style="background:#d7261f"></span>
</div>

<!-- specializes -->
<div class="abs sec-mark" style="left:587px;top:840px"></div>
<h2 class="abs sec-title" style="top:862px">We are <em>specializes</em> For Summit</h2>

<div class="abs spec-box" style="left:215px">
  <svg width="66" height="62" viewBox="0 0 66 62" fill="none" stroke="#f15a24" stroke-width="2.2"><path d="M6 30L33 8l27 22"/><path d="M12 26v32h42V26"/><rect x="24" y="36" width="18" height="22"/><path d="M33 2c5 6 8 9 4 14 3-1 6-4 6-8 5 6 5 12 0 16"/></svg>
  <p>Water and Fire<br>Damage</p>
</div>
<div class="abs spec-box" style="left:485px">
  <svg width="70" height="62" viewBox="0 0 70 62" fill="none" stroke="#f15a24" stroke-width="2.2"><path d="M4 30L35 6l31 24"/><path d="M12 25v33h46V25"/><rect x="20" y="36" width="12" height="22"/><rect x="38" y="34" width="14" height="12"/><path d="M50 12V4h6v12"/></svg>
  <p>Residential<br>ReModels</p>
</div>
<div class="abs spec-box" style="left:755px">
  <svg width="70" height="62" viewBox="0 0 70 62" fill="none" stroke="#f15a24" stroke-width="2.2"><path d="M8 58V34L34 18l28 16v24z"/><path d="M14 58l20-24 20 24M22 58l12-14 12 14"/><circle cx="10" cy="12" r="6"/><path d="M10 18v16"/><circle cx="58" cy="12" r="6"/><path d="M58 18v14"/><path d="M2 58h66"/></svg>
  <p>Landscaping and<br>Building ADU</p>
</div>

<!-- who we are -->
<section class="abs who">
  <div class="ph" style="left:131px;top:87px;width:290px;height:230px;background:linear-gradient(160deg,#3b4f7a 0%,#d98a3a 55%,#3a2a1e 100%)" role="img" aria-label="Two engineers in hard hats at sunset on a construction site"></div>
  <div class="ph" style="left:421px;top:123px;width:121px;height:9px;background:var(--orange)"></div>
  <div class="ph" style="left:421px;top:123px;width:121px;height:312px;background:linear-gradient(180deg,#4a3a33 0%,#a98a6d 50%,#e9e7e5 100%)" role="img" aria-label="Worker in hard hat silhouetted against steel framework"></div>
  <div class="ph" style="left:131px;top:322px;width:147px;height:173px;background:linear-gradient(150deg,#6b4a3e,#a8765e,#4a3530)" role="img" aria-label="Upward view of scaffolding on a building"></div>
  <div class="ph" style="left:286px;top:322px;width:256px;height:173px;background:linear-gradient(90deg,#c9c9c9,#f2f2f2)" role="img" aria-label="Hard hat and safety gear on a light background"></div>

  <div class="abs sec-mark" style="left:640px;top:127px"></div>
  <div class="abs" style="left:624px;top:150px">
    <h2>Who <em>We</em> Are</h2>
    <div class="sub">We Deliver Landmark Projects</div>
    <p class="para">We are rethoric question ran over her cheek When she reached the first hills of the Italic Mountains, she had a last view back on the skyline of her hometown Bookmarksgrove, the headline of Alphabet Village and the subline of her own road, the Line Lane.</p>
    <div class="feat"><span>We've Reputation For Excellence</span><span>We Build Partnerships</span><span>Guided By Commitment</span><span>A Team Of Professionals</span></div>
  </div>
</section>

<!-- what we do -->
<div class="abs sec-mark" style="left:587px;top:1915px"></div>
<h2 class="abs sec-title" style="top:1945px">What <em>We</em> Do</h2>

<div class="abs work-img" style="left:119px;top:2020px;background:linear-gradient(180deg,#7fb4e0,#c9a878 55%,#8a6a48)" role="img" aria-label="Row of new timber-framed houses under construction"></div>
<div class="abs work-label" style="left:119px;top:2212px">Home Construction</div>
<div class="abs work-img" style="left:445px;top:2020px;background:linear-gradient(180deg,#68a8e6,#e8e8e6 50%,#5f9a3a)" role="img" aria-label="White farmhouse exterior with green lawn"></div>
<div class="abs work-label" style="left:445px;top:2212px">Exterior Design</div>
<div class="abs work-img" style="left:771px;top:2020px;background:linear-gradient(90deg,#d8d8d6,#f1f1ef,#bdbcba)" role="img" aria-label="Remodeled white bathroom with vanity"></div>
<div class="abs work-label" style="left:771px;top:2212px">Building Remodeling</div>

<div class="abs work-img" style="left:119px;top:2258px;background:linear-gradient(90deg,#d6d2cc,#f2efea 50%,#c79a6a)" role="img" aria-label="Room under renovation with ladder"></div>
<div class="abs work-label" style="left:119px;top:2451px">Renovations</div>
<div class="abs work-img" style="left:445px;top:2258px;background:linear-gradient(90deg,#2f4f9a,#e8e4dc 55%,#d9a02e)" role="img" aria-label="Living room with blue sofa and yellow armchair"></div>
<div class="abs work-label" style="left:445px;top:2451px">Interior Design</div>
<div class="abs work-img" style="left:771px;top:2258px;background:linear-gradient(180deg,#dfe3e8,#a7acb3 60%,#555a60)" role="img" aria-label="Engineers supervising a site with cranes"></div>
<div class="abs work-label" style="left:771px;top:2451px">Safety Management</div>

<!-- stats -->
<div class="abs stats" role="img" aria-label="Orange-tinted construction site with excavator and workers"></div>
<div class="abs stat" style="left:90px;top:2680px"><div class="num">53</div><div class="lab">TOTAL PROJECTS</div></div>
<div class="abs stat" style="left:343px;top:2680px"><div class="num">371</div><div class="lab">STAFF MEMBERS</div></div>
<div class="abs stat" style="left:595px;top:2680px"><div class="num">15</div><div class="lab">WORKING IN STATES</div></div>
<div class="abs stat" style="left:848px;top:2680px"><div class="num">2,600</div><div class="lab">HOURS FOR WORK</div></div>

<!-- testimonials -->
<div class="abs sec-mark" style="left:587px;top:2955px"></div>
<h2 class="abs sec-title" style="top:2984px">What Our <em>Happy Clients</em> Said About us</h2>

<div class="abs avatar" style="left:110px;top:3073px;background:radial-gradient(circle at 50% 40%,#b58c72,#6f5a4d 60%,#8e9296)" role="img" aria-label="Portrait of client Daniel Reeve"></div>
<p class="abs quote" style="left:309px;top:3077px">"...and for all the wonderful work you and your crew are doing. Our team has nothing but good things to say - we are really fortunate to have found you for this project!"</p>
<div class="abs t-name" style="left:309px;top:3218px">Daniel Reeve</div>
<div class="abs stars" style="left:464px;top:3215px">★★★★★</div>

<div class="abs" style="left:598px;top:3080px;width:1px;height:170px;background:var(--line)"></div>

<p class="abs quote" style="left:631px;top:3077px">Summit Builders is one of the best general contractors we've worked with. The entire team tactfully delivered a project of exceptional quality while staying on schedule !"</p>
<div class="abs t-name" style="left:631px;top:3218px">Alina Park</div>
<div class="abs stars" style="left:786px;top:3215px">★★★★★</div>
<div class="abs avatar" style="left:920px;top:3073px;background:radial-gradient(circle at 50% 40%,#e3b9a0,#3a2a26 60%,#d9d9d9)" role="img" aria-label="Portrait of client Alina Park"></div>

<div class="abs dots" style="left:576px;top:3290px"><span></span><span class="on"></span><span></span></div>
<div class="abs" style="left:111px;top:3331px;width:978px;height:1px;background:var(--line)"></div>

<!-- recent projects -->
<div class="abs sec-mark" style="left:587px;top:3396px"></div>
<h2 class="abs sec-title" style="top:3426px">Our <em>Recent</em> Project</h2>

<div class="proj" style="left:108px;top:3525px;width:319px;height:322px;background:linear-gradient(180deg,#eef3e0,#d9c05a 45%,#4f8a2a)" role="img" aria-label="Large yellow villa with landscaped garden"></div>
<div class="proj" style="left:108px;top:3856px;width:319px;height:154px;background:linear-gradient(90deg,#e0d4c2,#c9b9a4 50%,#3b4a6a)" role="img" aria-label="High school building facade"></div>
<div class="proj" style="left:438px;top:3525px;width:315px;height:155px;background:linear-gradient(135deg,#2a2a2c,#4a7a9a 50%,#2e2e30)" role="img" aria-label="Aerial view of house interior under construction"></div>
<div class="proj" style="left:762px;top:3525px;width:318px;height:155px;background:linear-gradient(180deg,#4a78b8,#d9d4cc 55%,#8a6a52)" role="img" aria-label="Two-storey suburban home with blue sky"></div>
<div class="proj" style="left:438px;top:3690px;width:642px;height:320px;background:linear-gradient(180deg,#6a5a78 0%,#c98a6a 35%,#59647a 60%,#6e6e72 100%)" role="img" aria-label="Modern grey house at dusk with lit windows"></div>

<!-- footer -->
<footer class="abs footer">
  <div class="abs logo" style="left:155px;top:108px"><span class="mark"></span><span class="name">Summit Builders</span></div>
  <p class="abs f-text" style="left:108px;top:158px;width:400px">Sed porttitor lectus nibh. Donec rutrum congue leo eget malesuada.</p>
  <div class="abs license" style="left:111px;top:222px">CSLB License # 2418596</div>

  <h4 class="abs" style="left:544px;top:78px">QUICK LINKS</h4>
  <ul class="abs ql" style="left:550px;top:124px"><li>Home</li><li>About us</li><li>Services</li><li>Projects/ Portfolio</li><li>Contact us</li></ul>

  <h4 class="abs" style="left:776px;top:78px">CONTACT INFO</h4>
  <ul class="abs ci" style="left:770px;top:124px;width:300px">
    <li><svg width="12" height="16" viewBox="0 0 24 32" style="margin-top:5px;flex:none"><path fill="#fff" d="M12 0a12 12 0 0112 12c0 9-12 20-12 20S0 21 0 12A12 12 0 0112 0zm0 7a5 5 0 100 10 5 5 0 000-10z"/></svg><span style="margin-left:8px">1520 Ridgeview Ave Fairmont,<br>CA 92705</span></li>
    <li><svg width="16" height="12" viewBox="0 0 24 18" style="margin-top:7px;flex:none"><path fill="#fff" d="M0 0h24v18H0z"/><path fill="none" stroke="#0b1030" stroke-width="2" d="M1 1l11 9 11-9"/></svg><span style="margin-left:4px">info@summitbuildersca.example</span></li>
    <li><svg width="14" height="14" viewBox="0 0 24 24" style="margin-top:6px;flex:none"><path fill="#fff" d="M6.6 10.8a15 15 0 006.6 6.6l2.2-2.2a1 1 0 011-.25 11 11 0 003.6.6 1 1 0 011 1V20a1 1 0 01-1 1A17 17 0 013 4a1 1 0 011-1h3.5a1 1 0 011 1 11 11 0 00.6 3.6 1 1 0 01-.25 1z"/></svg><span style="margin-left:6px">+1 555 014 2207</span></li>
  </ul>
</footer>
<div class="abs rule" style="left:100px;top:4386px;width:1000px;height:1px;background:#2a3058"></div>
<div class="abs" style="left:0;top:4408px;width:1200px;text-align:center;color:#fff;font-family:'Poppins',sans-serif;font-size:16px">© Copyrights 2020 &nbsp;Summit &nbsp;| &nbsp;All Rights Reserved</div>

</body>
</html>
```